Verodex business card

Business card for sustainable investment company called "Verodex". Verodex is an exchange platform selling carbon credits between buyers and sellers. Carbon Credits are an environmental commodity for reducing global carbon emissions.

the card should obviously have our logo and the theme should be sustainability/environment mixed with a trading platform.

Contact Information for Business Card

Logo, Name, Title, Phone, Email

Colors
0054AA
0677BA
7BADD7
CADEEF
E8F1F8
0094D4
00A9DD
6FCCEA
C7EBF8
E9F6FB
00AB8E
00BBA5
67D7C9
C6EFE9
E9F9F6
59FF00
82FF00
B8FF75
E3FFCB
F4FFEA

```html
<!DOCTYPE html>
<html lang="en">
<head>
<meta charset="UTF-8">
<title>Verodex Business Card</title>
<link href="https://fonts.googleapis.com/css2?family=Montserrat:wght@400;500;700;800&display=swap" rel="stylesheet">
<style>
  :root {
    --navy: #14295a;
    --navy-deep: #0f2250;
    --sky: #2fa8e6;
    --sky-light: #4ec3ea;
    --blue: #3a78c8;
    --ink: #1b2a4a;
    --paper: #ffffff;
    --backdrop: #e6e8ec;
  }
  * { box-sizing: border-box; margin: 0; padding: 0; }
  html, body {
    width: 1200px; height: 900px; overflow: hidden;
    background: var(--backdrop);
    font-family: "Montserrat", sans-serif;
  }
  .stage {
    position: relative; width: 1200px; height: 900px;
    display: flex; flex-direction: column; align-items: center; justify-content: center; gap: 56px;
  }
  .card {
    position: relative; width: 580px; height: 331px; overflow: hidden;
    box-shadow: 0 10px 26px rgba(0,0,0,.18);
  }
  /* Front */
  .card--front {
    background: linear-gradient(120deg, var(--navy-deep) 0%, #1d3568 55%, var(--navy) 100%);
    display: flex; align-items: center; justify-content: center;
  }
  .brand { display: flex; align-items: center; gap: 18px; }
  .brand__dot { width: 34px; height: 34px; background: var(--sky); }
  .brand__name { font-weight: 700; letter-spacing: 2px; line-height: 1; }
  .card--front .brand__name { color: var(--paper); font-size: 62px; }
  .card--front .brand__dot { width: 46px; height: 46px; }

  /* Back */
  .card--back { background: var(--paper); }
  .card--back .brand { position: absolute; left: 118px; top: 78px; }
  .card--back .brand__name { color: var(--ink); font-size: 48px; }
  .card--back .brand__dot { width: 38px; height: 38px; }

  .details { position: absolute; left: 118px; top: 160px; display: flex; gap: 22px; }
  .person { text-align: right; padding-top: 4px; }
  .person__name { font-weight: 800; font-size: 23px; letter-spacing: .5px; }
  .person__first { color: var(--sky); }
  .person__last { color: var(--ink); }
  .person__title { font-weight: 500; font-size: 16px; color: #222; margin-top: 4px; }
  .divider { width: 1.5px; height: 78px; background: var(--sky); }
  .contacts { list-style: none; display: flex; flex-direction: column; gap: 6px; padding-top: 2px; }
  .contacts li { display: flex; align-items: center; gap: 9px; font-size: 14.5px; color: #1a1a1a; font-weight: 500; }
  .contacts svg { width: 15px; height: 15px; flex: none; }
  .card__bands { position: absolute; left: 0; bottom: 0; width: 580px; height: 110px; }
</style>
</head>
<body>
<main class="stage">
  <section class="card card--front" aria-label="Card front">
    <div class="brand">
      <span class="brand__dot"></span>
      <span class="brand__name">VERODEX</span>
    </div>
  </section>

  <section class="card card--back" aria-label="Card back">
    <div class="brand">
      <span class="brand__dot"></span>
      <span class="brand__name">VERODEX</span>
    </div>
    <div class="details">
      <div class="person">
        <div class="person__name"><span class="person__first">DANIEL</span> <span class="person__last">MARSH</span></div>
        <div class="person__title">Co-Founder</div>
      </div>
      <div class="divider"></div>
      <ul class="contacts">
        <li>
          <svg viewBox="0 0 16 16"><path d="M3 2h3l1.5 3.5-2 1.2a8 8 0 0 0 3.8 3.8l1.2-2L14 10v3a1.5 1.5 0 0 1-1.5 1.5A11.5 11.5 0 0 1 1.5 3.5 1.5 1.5 0 0 1 3 2z" fill="#2fa8e6"/></svg>
          555-210-4476
        </li>
        <li>
          <svg viewBox="0 0 16 16"><rect x="1" y="3.5" width="14" height="9" fill="#2fa8e6"/><path d="M1 3.5l7 5 7-5" stroke="#fff" stroke-width="1.3" fill="none"/></svg>
          info@verodex.com
        </li>
        <li>
          <svg viewBox="0 0 16 16"><circle cx="8" cy="8" r="6.5" fill="#2fa8e6"/><path d="M1.5 8h13M8 1.5c-3 3.5-3 9.5 0 13M8 1.5c3 3.5 3 9.5 0 13" stroke="#fff" stroke-width="1" fill="none"/></svg>
          www.verodex.com
        </li>
      </ul>
    </div>
    <svg class="card__bands" viewBox="0 0 580 110" preserveAspectRatio="none" aria-hidden="true">
      <defs>
        <linearGradient id="bandGrad" x1="0" y1="0" x2="1" y2="0">
          <stop offset="0" stop-color="#4ec3ea"/>
          <stop offset="0.6" stop-color="#2fa8e6"/>
          <stop offset="1" stop-color="#3a78c8"/>
        </linearGradient>
      </defs>
      <polygon points="0,96 395,96 384,110 0,110" fill="#14295a"/>
      <polygon points="409,78 580,78 580,110 390,110" fill="url(#bandGrad)"/>
    </svg>
  </section>
</main>
</body>
</html>
```